Flyer for the Radiant Harvest Worship Day

I am looking to create a flyer for a one day prayer retreat our church is organizing.
This flyer will be posted on social media, websites and will also be printed so it can be mailed to people.
I am looking for something professional, with good use of our logo and band colors (logo colors).
I am counting on the designer's skill, creativity, art and knowledge of media communication to produce a flyer that will effectively and quickly convey the message we are trying to spread.
CONTENT OF THE FLYER:
Event title: Radiant Harvest Worship Day
Date: Tuesday July 2nd, 2019
Time: 11:00AM - 7:00PM
Belmora Hotel, 4875 Wexley Avenue, Portland, Maine 04102 (Room: Juniper)
Event Key words to highlight what the event is about: Prayer, Sharing the Word, Panel discussion, prophecy, Impartation.
Key phrases:
A one day prayer retreat.
Jesus Chris is Lord
Contact info:
www.tolvex.org
Phone: 207 555 3184
Email: contact@brookhavenfold.org

```html
<!DOCTYPE html>
<html lang="en">
<head>
<meta charset="utf-8">
<title>Radiant Harvest Worship Day – Flyer</title>
<link rel="stylesheet" href="https://fonts.googleapis.com/css2?family=Arimo:wght@400;700&display=swap">
<style>
  :root {
    --navy: #0b3358;
    --steel: #1e5d86;
    --orange: #f39a2b;
    --white: #ffffff;
    --paper: #ffffff;
    --edge: #9a9a9a;
    --sky-top: #c9c3bd;
    --sky-mid: #f2c58e;
    --sun: #fff1c9;
    --grass: #4a3526;
    --rule: #8fa3b8;
  }
  * { box-sizing: border-box; margin: 0; padding: 0; }
  html, body { width: 879px; height: 1200px; overflow: hidden; background: var(--paper); }
  body { font-family: "Arimo", Arial, Helvetica, sans-serif; position: relative; border: 1px solid var(--edge); }

  .flyer {
    position: absolute; left: 45px; top: 38px; width: 780px; height: 1102px;
    background: var(--navy); overflow: hidden; border: 1px solid #6c6c6c;
  }
  .hero-photo {
    position: absolute; left: 0; top: 0; width: 780px; height: 620px;
    background:
      radial-gradient(circle at 73% 66%, var(--sun) 0 4%, rgba(255,220,160,.7) 12%, rgba(255,220,160,0) 38%),
      linear-gradient(180deg, var(--sky-top) 0%, #e6d3bf 30%, var(--sky-mid) 58%, #d99b5a 74%, var(--grass) 100%);
  }
  .waves { position: absolute; left: 0; top: 0; width: 780px; height: 1102px; }

  .brand-box {
    position: absolute; left: 52px; top: 0; width: 204px; height: 204px;
    background: var(--navy); display: flex; align-items: center; justify-content: center; gap: 10px;
  }
  .brand-name { color: var(--white); font-weight: 400; font-size: 36px; letter-spacing: 1px; }
  .brand-dot { width: 14px; height: 14px; border-radius: 50%; background: var(--orange); }

  .event-title { position: absolute; left: 42px; top: 276px; font-weight: 700; }
  .event-title .line-1 { display: block; color: var(--navy); font-size: 41px; line-height: 46px; }
  .event-title .line-2 { display: block; color: var(--orange); font-size: 56px; line-height: 62px; margin-top: 4px; }

  .tagline { position: absolute; left: 0; top: 656px; width: 780px; text-align: center; }
  .tagline .lead { color: var(--white); font-size: 33px; line-height: 38px; font-weight: 400; }
  .tagline .claim { color: var(--orange); font-size: 50px; line-height: 56px; font-weight: 700; margin-top: 4px; }

  .details { position: absolute; left: 0; top: 802px; width: 780px; color: var(--white); font-size: 21px; }
  .details .row { display: flex; justify-content: center; align-items: center; height: 40px; }
  .details .row + .row { margin-top: 12px; }
  .details .item { display: flex; align-items: center; gap: 10px; }
  .details .item + .item { margin-left: 18px; }
  .details .address { font-size: 19px; }
  .icon { width: 34px; height: 34px; flex: none; }

  .keywords {
    position: absolute; left: 0; top: 914px; width: 780px; text-align: center;
    color: var(--orange); font-size: 17px; line-height: 24px; font-weight: 700; letter-spacing: .5px;
  }

  .footer { position: absolute; left: 33px; top: 957px; width: 715px; height: 120px; }
  .footer .rule { position: absolute; left: 0; right: 0; top: 30px; height: 1px; background: var(--rule); }
  .footer .brand {
    position: absolute; left: 14px; top: 12px; padding: 0 14px; background: var(--navy);
    display: flex; align-items: center; gap: 10px; height: 80px;
  }
  .footer .brand .brand-name { font-size: 38px; }
  .contacts { position: absolute; left: 240px; top: 42px; color: var(--white); font-size: 28px; line-height: 36px; }
  .contacts .line { display: flex; align-items: center; gap: 10px; }
  .contacts .small-icon { width: 26px; height: 26px; flex: none; }
</style>
</head>
<body>
  <main class="flyer">
    <div class="hero-photo" role="img" aria-label="Photo of a woman in silhouette raising her arms at sunset in a grassy field while doves fly overhead"></div>

    <svg class="waves" viewBox="0 0 780 1102" aria-hidden="true">
      <path d="M0,505 C220,610 560,590 780,262 L780,1102 L0,1102 Z" fill="var(--orange)"/>
      <path d="M0,510 C230,585 560,560 780,360 L780,1102 L0,1102 Z" fill="var(--steel)"/>
      <path d="M0,520 C240,575 560,555 780,448 L780,1102 L0,1102 Z" fill="var(--navy)"/>
    </svg>

    <div class="brand-box">
      <span class="brand-dot"></span>
      <span class="brand-name">TOLVEX</span>
    </div>

    <h1 class="event-title">
      <span class="line-1">RADIANT HARVEST</span>
      <span class="line-2">WORSHIP DAY</span>
    </h1>

    <section class="tagline">
      <p class="lead">A ONE DAY PRAYER RETREAT.</p>
      <p class="claim">JESUS CHRIS IS LORD</p>
    </section>

    <section class="details">
      <div class="row">
        <div class="item">
          <svg class="icon" viewBox="0 0 34 34" aria-hidden="true">
            <circle cx="17" cy="17" r="17" fill="var(--orange)"/>
            <rect x="9" y="10" width="16" height="15" rx="1.5" fill="none" stroke="#fff" stroke-width="1.6"/>
            <line x1="9" y1="14.5" x2="25" y2="14.5" stroke="#fff" stroke-width="1.6"/>
            <line x1="13" y1="8" x2="13" y2="12" stroke="#fff" stroke-width="1.6"/>
            <line x1="21" y1="8" x2="21" y2="12" stroke="#fff" stroke-width="1.6"/>
            <g fill="#fff"><rect x="12" y="17" width="2" height="2"/><rect x="16" y="17" width="2" height="2"/><rect x="20" y="17" width="2" height="2"/><rect x="12" y="21" width="2" height="2"/><rect x="16" y="21" width="2" height="2"/></g>
          </svg>
          <span>Tuesday July 2nd, 2019</span>
        </div>
        <div class="item">
          <svg class="icon" viewBox="0 0 34 34" aria-hidden="true">
            <circle cx="17" cy="17" r="17" fill="var(--orange)"/>
            <circle cx="17" cy="17" r="8.5" fill="none" stroke="#fff" stroke-width="1.6"/>
            <polyline points="17,12 17,17 21,19" fill="none" stroke="#fff" stroke-width="1.6" stroke-linecap="round"/>
          </svg>
          <span>11:00AM - 7:00PM</span>
        </div>
      </div>
      <div class="row">
        <div class="item address">
          <svg class="icon" viewBox="0 0 34 34" aria-hidden="true">
            <circle cx="17" cy="17" r="17" fill="var(--orange)"/>
            <path d="M17,26 C12,20 11,17 11,14.5 A6,6 0 0 1 23,14.5 C23,17 22,20 17,26 Z" fill="none" stroke="#fff" stroke-width="1.6"/>
            <circle cx="17" cy="14.5" r="2.2" fill="none" stroke="#fff" stroke-width="1.6"/>
          </svg>
          <span>Belmora Hotel, Room Juniper, 4875 Wexley Avenue, Portland, Maine 04102</span>
        </div>
      </div>
    </section>

    <p class="keywords">PRAYER • SHARING THE WORD • PANEL DISCUSSION • PROPHECY • IMPARTATION</p>

    <footer class="footer">
      <div class="rule"></div>
      <div class="brand">
        <span class="brand-dot"></span>
        <span class="brand-name">TOLVEX</span>
      </div>
      <div class="contacts">
        <div class="line">
          <svg class="small-icon" viewBox="0 0 26 26" aria-hidden="true">
            <g fill="none" stroke="#fff" stroke-width="1.4">
              <circle cx="13" cy="13" r="10"/><ellipse cx="13" cy="13" rx="4.5" ry="10"/>
              <line x1="3" y1="13" x2="23" y2="13"/><line x1="5" y1="8" x2="21" y2="8"/><line x1="5" y1="18" x2="21" y2="18"/>
            </g>
          </svg>
          <span>tolvex.org</span>
          <svg class="small-icon" viewBox="0 0 26 26" aria-hidden="true" style="margin-left:10px">
            <g fill="none" stroke="#fff" stroke-width="1.4">
              <path d="M3,10 C3,6 23,6 23,10 L20,12 L17,10 L9,10 L6,12 Z"/>
              <path d="M8,12 L6,21 L20,21 L18,12"/><circle cx="13" cy="16" r="2.5"/>
            </g>
          </svg>
          <span>207 555 3184</span>
        </div>
        <div class="line">
          <svg class="small-icon" viewBox="0 0 26 26" aria-hidden="true">
            <g fill="none" stroke="#fff" stroke-width="1.4">
              <rect x="3" y="6" width="20" height="14"/><polyline points="3,6 13,14 23,6"/>
            </g>
          </svg>
          <span>contact@brookhavenfold.org</span>
        </div>
      </div>
    </footer>
  </main>
</body>
</html>
```